Modern Business Card for Larkwell 2018

Our company assumes the best about people. We are creating an online community of entrepreneurs and business leaders who struggle with marketing their business online.

This business card should POP! We recently got a new logo and are launching a new website next month, so our business cards should make a statement that feels:
-Fresh
-Smart
-Trustworthy
-Fun

Target Market(s)

small business owners, entrepreneurs

Industry/Entity Type

Digital Marketing

Contact Information for Business Card

Dimensions: 3.5" x 2"

Font styles to use
Sans Serif

Colors
f37122
ffffff

Requirements
Must have
• We need a business card with a modern, bold design. We will use one side of the card as a lead-generation offer, so text on one side will need to fit up to 140 characters. The business card should stick to our core colors (orange, black, and white).
Nice to have
• We think a vertical "portrait" design could be interesting.
Should not have
• Should not look like a traditional business card. The round icon should stand out from a distance.

```html
<!DOCTYPE html>
<html lang="en">
<head>
<meta charset="utf-8">
<title>Larkwell Business Card</title>
<link rel="stylesheet" href="https://fonts.googleapis.com/css2?family=Barlow:wght@400;500;700&family=Merriweather:ital,wght@1,700&display=swap">
<style>
  :root {
    --orange: #f37122;
    --white: #ffffff;
    --charcoal: #353334;
    --ink: #2a2a2a;
    --backdrop: #d9d9d9;
  }
  * { margin: 0; padding: 0; box-sizing: border-box; }
  html, body {
    width: 1200px; height: 1200px; overflow: hidden;
    background: var(--backdrop);
  }
  .stage {
    position: absolute; left: 0; top: 0;
    width: 1490px; height: 1490px;
    transform: scale(0.80537); transform-origin: 0 0;
  }
  .card {
    position: absolute; left: 272px;
    width: 946px; height: 539px;
    overflow: hidden;
    box-shadow: 0 24px 30px rgba(0,0,0,0.25);
  }
  /* Front */
  .card-front { top: 130px; background: var(--white); }
  .front-panel { position: absolute; inset: 0; width: 100%; height: 100%; }
  .holder-name {
    position: absolute; left: 56px; top: 284px;
    font-family: "Barlow", sans-serif; font-weight: 700;
    font-size: 50px; line-height: 62px;
    color: var(--ink); letter-spacing: 1px;
  }
  .holder-title {
    position: absolute; left: 46px; top: 424px;
    font-family: "Barlow", sans-serif; font-weight: 500;
    font-size: 28px; color: #3a3a3a;
  }
  .holder-email {
    position: absolute; left: 46px; top: 460px;
    font-family: "Barlow", sans-serif; font-weight: 400;
    font-size: 31px; color: #3a3a3a; letter-spacing: 0.5px;
  }
  /* Back */
  .card-back { top: 779px; background: var(--charcoal); }
  .brand-band {
    position: absolute; left: 0; top: 0; width: 100%; height: 217px;
    background: var(--orange);
  }
  .brand-dot {
    position: absolute; left: 50%; top: 52px;
    width: 72px; height: 72px; margin-left: -36px;
    border-radius: 50%; background: var(--white);
  }
  .brand-name {
    position: absolute; left: 0; right: 0; top: 128px;
    text-align: center;
    font-family: "Barlow", sans-serif; font-weight: 700;
    font-size: 86px; line-height: 86px;
    color: var(--white); letter-spacing: 1px;
  }
  .tagline {
    position: absolute; left: 0; right: 0; top: 222px;
    text-align: center;
    font-family: "Merriweather", serif; font-style: italic; font-weight: 700;
    font-size: 27px; color: var(--white);
  }
  .accent-rule {
    position: absolute; left: 0; top: 266px; width: 100%; height: 3px;
    background: var(--orange);
  }
  .offer {
    position: absolute; left: 0; right: 0; top: 372px;
    text-align: center;
    font-family: "Barlow", sans-serif; font-weight: 500;
    font-size: 26px; line-height: 34px; color: var(--white);
  }
  .offer-url {
    display: block; margin-top: 8px;
    font-size: 40px; line-height: 44px; letter-spacing: 1px;
  }
</style>
</head>
<body>
  <main class="stage">
    <section class="card card-front">
      <svg class="front-panel" viewBox="0 0 946 539" aria-hidden="true">
        <circle cx="728" cy="255" r="362" fill="var(--orange)"/>
      </svg>
      <h1 class="holder-name">DANA<br>WHITFIELD</h1>
      <p class="holder-title">Story Marketing Coach</p>
      <p class="holder-email">dana@larkwellnow.com</p>
    </section>

    <section class="card card-back">
      <div class="brand-band">
        <span class="brand-dot"></span>
        <h2 class="brand-name">LARKWELL</h2>
      </div>
      <p class="tagline">Tell Stories That Inspire Action</p>
      <div class="accent-rule"></div>
      <p class="offer">Get your free Larkwell Starter Package and<br>our marketing guide today at
        <span class="offer-url">larkwellnow.com/start</span>
      </p>
    </section>
  </main>
</body>
</html>
```